App UI design needed! For a Password Management Tool

Need a design of a Windows desktop application which is a Password Management Tool, similar to 9tidewell, Quillmark or Brimsoft, with Business/Enterprise functionalities. Here attached are a few sample pages of Quillmark, and some sample pages of our app called Veltrika. We certainly want to redesign our app.
We need: 1. The layout of the web: top banner, menu, main pane; 2. Form style, main form and sub forms; 3. List style; 4 Fonts and buttons; 5. Logo.
The design should look professional, can attract business customers as well as individual users, and present a strong sense of “Security”. The look and feel should differentiate from well-known products like 9tidewell, Quillmark, Brimsoft, etc.

```html
<!DOCTYPE html>
<html lang="en">
<head>
<meta charset="utf-8">
<title>Veltrika – Web Logins</title>
<link rel="stylesheet" href="https://fonts.googleapis.com/css2?family=Inter:wght@400;500;600&display=swap">
<style>
:root{
  --stage:#8787fc;
  --blue:#0a8bf2;
  --green:#22d38a;
}
*{box-sizing:border-box;margin:0;padding:0}
html,body{width:1175px;height:1200px;overflow:hidden}
body{background:var(--stage);font-family:"Inter",sans-serif;position:relative}

.win{position:absolute;width:798px;height:498px;border-radius:9px;overflow:hidden;background:var(--win-bg);color:var(--text)}
.win--dark{left:61px;top:79px;
  --win-bg:#14142f;--pane:#25254a;--card:#17173a;--head-band:#20204a;--hover:#2c2c56;
  --text:#ffffff;--muted:#c9c9e0;--search:#25254a;--search-text:#c4c4dc;--line:#2e2e55;
  --check:#6a6a90;--active-bg:#1d1d45;--tip-bg:#3b3b5e;--tip-text:#fff;--hover-icon:#4a4a70;--row-weight:500;--version:#c9c9e0}
.win--light{left:316px;top:622px;box-shadow:0 4px 18px rgba(40,40,120,.15);
  --win-bg:#ffffff;--pane:#eef0fc;--card:#ffffff;--head-band:transparent;--hover:#f2f3fb;
  --text:#16163a;--muted:#6b6bb0;--search:#e9eafb;--search-text:#a6a8c8;--line:#e4e5f0;
  --check:#c9cade;--active-bg:#ffffff;--tip-bg:#16163a;--tip-text:#fff;--hover-icon:transparent;--row-weight:400;--version:#a6a8c8}

.abs{position:absolute}
.logo{left:10px;top:22px;width:102px;height:22px;background:#14142f;display:flex;align-items:center;gap:4px;padding-left:6px;color:#3ba3ff;font-size:12px;font-weight:600}
.logo-dot{width:10px;height:10px;border-radius:50%;background:#3ba3ff}
.win--dark .logo{background:#26263a}

.search{left:160px;top:20px;width:319px;height:25px;border-radius:5px;background:var(--search);color:var(--search-text);font-size:8.6px;display:flex;align-items:center;padding:0 12px 0 17px;justify-content:space-between}

.top-icon{top:24px;width:18px;height:18px}
.avatar{left:735px;top:21px;width:24px;height:24px;border-radius:50%;background:radial-gradient(circle at 50% 40%,#7a5a48,#2a1d18);border:2px solid #3b8cd9}
.caret{left:765px;top:31px;width:0;height:0;border-left:3.5px solid transparent;border-right:3.5px solid transparent;border-top:4px solid var(--green)}

.nav{left:7px;top:69px;width:146px;list-style:none}
.nav-item{height:34px;display:flex;align-items:center;gap:9px;padding-left:9px;font-size:9.3px;font-weight:500;border-radius:5px}
.nav-item svg{width:13px;height:13px;flex:none}
.nav-item--active{background:var(--active-bg);border:1px solid var(--blue)}
.version{left:10px;top:484px;font-size:7.8px;color:var(--version)}

.pane{left:160px;top:67px;width:638px;height:431px;background:var(--pane);border-top-left-radius:8px}
.page-title{left:17px;top:12px;font-size:12.5px;font-weight:500}
.page-sub{left:17px;top:30px;font-size:8.7px;color:var(--muted)}
.btn-new{left:535px;top:9px;width:75px;height:29px;border-radius:5px;background:var(--blue);color:#fff;font-size:9.3px;font-weight:500;display:flex;align-items:center;justify-content:center;gap:5px;box-shadow:0 5px 10px rgba(10,139,242,.35)}

.card{left:17px;top:54px;width:596px;height:363px;background:var(--card);border-radius:6px}
.card-title{left:17px;top:15px;font-size:12px;font-weight:500}
.card-meta{top:18px;font-size:7.8px;color:var(--muted)}
.page-box{display:inline-block;padding:1px 5px;margin:0 4px;border-radius:3px}
.win--light .page-box{background:var(--pane)}

.row{position:absolute;left:7px;width:582px;height:34px;font-size:9.3px;border-radius:5px}
.row span{position:absolute;top:50%;transform:translateY(-50%);white-space:nowrap}
.row--head{left:0;width:596px;top:38px;height:29px;background:var(--head-band);border-radius:0;font-weight:500;font-size:9px}
.row--head .c-check{left:17px}.row--head .c-name{left:41px}.row--head .c-user{left:168px}.row--head .c-url{left:321px}
.row--hover{background:var(--hover)}
.c-check{left:10px;width:11px;height:11px;border:1px solid var(--check);border-radius:3px}
.c-icon{left:34px;width:15px;height:15px;border-radius:50%;background:#7f8aa8}
.c-name{left:55px;font-weight:500}
.c-user{left:161px;font-weight:var(--row-weight)}
.c-url{left:314px;font-weight:var(--row-weight)}
.row--hover .c-user,.row--hover .c-url{font-weight:500}
.win--light .row--hover .c-user,.win--light .row--hover .c-url{font-weight:400}
.act{width:13px;height:13px}
.act-open{left:484px;width:24px;height:24px;border-radius:50%;background:var(--hover-icon);display:flex;align-items:center;justify-content:center}
.act-edit{left:523px}.act-del{left:553px}
.divider{left:16px;width:573px;height:1px;background:var(--line)}
.tooltip{left:471px;top:185px;width:37px;height:18px;border-radius:3px;background:var(--tip-bg);color:var(--tip-text);font-size:8.6px;display:flex;align-items:center;justify-content:center}
</style>
</head>
<body>

<!-- Dark theme window -->
<section class="win win--dark">
  <div class="abs logo"><span class="logo-dot"></span>Veltrika</div>
  <div class="abs search">Find something...<svg width="11" height="11" viewBox="0 0 12 12" fill="none" stroke="currentColor" stroke-width="1.2"><circle cx="5.5" cy="5.5" r="4.3"/><path d="M8.6 8.6 11 11"/></svg></div>
  <svg class="abs top-icon" style="left:630px" viewBox="0 0 18 18"><path d="M9 2a5 5 0 0 0-5 5v4l-1.5 2.5h13L14 11V7a5 5 0 0 0-5-5z" fill="var(--blue)"/><path d="M7 15a2 2 0 0 0 4 0z" fill="var(--blue)"/><circle cx="14" cy="3.5" r="2" fill="var(--green)"/></svg>
  <svg class="abs top-icon" style="left:685px" viewBox="0 0 18 18"><circle cx="9" cy="9" r="5.5" fill="none" stroke="var(--blue)" stroke-width="3.4" stroke-dasharray="2.6 1.7"/><circle cx="9" cy="9" r="4.4" fill="var(--blue)"/><circle cx="9" cy="9" r="1.8" fill="var(--win-bg)"/></svg>
  <div class="abs avatar" role="img" aria-label="User profile photo"></div>
  <div class="abs caret"></div>

  <ul class="abs nav">
    <li class="nav-item"><svg viewBox="0 0 13 13"><rect x="0" y="0" width="5" height="7" rx="1" fill="var(--blue)"/><rect x="0" y="8" width="5" height="5" rx="1" fill="var(--green)"/><rect x="7" y="0" width="6" height="13" rx="1" fill="var(--text)"/></svg>Dashboard</li>
    <li class="nav-item"><svg viewBox="0 0 13 13"><circle cx="6.5" cy="3.5" r="3" fill="var(--blue)"/><path d="M1 13a5.5 5 0 0 1 11 0z" fill="var(--blue)"/></svg>Users</li>
    <li class="nav-item"><svg viewBox="0 0 13 13"><circle cx="5" cy="3.5" r="2.8" fill="var(--blue)"/><path d="M0 12a5 4.5 0 0 1 10 0z" fill="var(--blue)"/><circle cx="10" cy="5" r="2" fill="var(--green)"/></svg>Teams</li>
    <li class="nav-item"><svg viewBox="0 0 13 13"><rect x="0" y="0" width="6" height="5" rx="1" fill="var(--blue)"/><rect x="7" y="8" width="6" height="5" rx="1" fill="var(--green)"/><path d="M3 5v5h4" stroke="var(--blue)" fill="none"/></svg>Client Containers</li>
    <li class="nav-item nav-item--active"><svg viewBox="0 0 13 13"><circle cx="6.5" cy="6.5" r="6" fill="var(--green)"/><path d="M.5 6.5h12M6.5.5c-3 3-3 9 0 12M6.5.5c3 3 3 9 0 12" stroke="var(--win-bg)" stroke-width=".9" fill="none"/></svg>Web Logins</li>
    <li class="nav-item"><svg viewBox="0 0 13 13"><path d="M2 0h6l3 3v10H2z" fill="var(--blue)"/><path d="M4 6h5M4 8h5M4 10h5" stroke="var(--win-bg)" stroke-width=".8"/></svg>Reports</li>
  </ul>
  <div class="abs version">Version 2.3.4</div>

  <main class="abs pane">
    <h1 class="abs page-title">Web Logins</h1>
    <p class="abs page-sub">Showing details of all the web logins saved in your system</p>
    <div class="abs btn-new"><svg width="8" height="8" viewBox="0 0 8 8" stroke="#fff" stroke-width="1.4"><path d="M4 0v8M0 4h8"/></svg>New</div>

    <div class="abs card">
      <h2 class="abs card-title">Lists</h2>
      <p class="abs card-meta" style="left:253px">Showing 1-10 of 354 items</p>
      <p class="abs card-meta" style="left:518px">Page<span class="page-box">1</span> / 36</p>

      <div class="row row--head"><span class="c-check"></span><span class="c-name">Name</span><span class="c-user">User name</span><span class="c-url">Login page URL</span></div>

      <div class="row" style="top:70px"><span class="c-check"></span><span class="c-icon" style="background:#1877f2"></span><span class="c-name">Kinfold</span><span class="c-user">rkestrel@inboxly.net</span><span class="c-url">https://www.kinfold.com</span></div>
      <div class="row row--hover" style="top:107px"><span class="c-check"></span><span class="c-icon" style="background:var(--text)"></span><span class="c-name">Codehive</span><span class="c-user">rkestrel@inboxly.net</span><span class="c-url">https://www.codehive.com/login</span>
        <span class="act-open"><svg class="act" viewBox="0 0 13 13" fill="none" stroke="var(--text)" stroke-width="1"><path d="M1 4V1h3M9 1h3v3M12 9v3H9M4 12H1V9"/><circle cx="5" cy="6.5" r="1.4"/><path d="M6.4 6.5H10"/></svg></span>
        <span class="act-edit"><svg class="act" viewBox="0 0 13 13" fill="none" stroke="var(--text)" stroke-width="1.1"><path d="M6 2H1.5v9.5H11V7"/><path d="M10 1l2 2-5.5 5.5H4.5v-2z"/></svg></span>
        <span class="act-del"><svg class="act" viewBox="0 0 13 13" fill="var(--text)"><rect x="1.5" y="1.5" width="10" height="1.6"/><rect x="5" y="0" width="3" height="1.5"/><path d="M2.5 4h8l-.7 9H3.2z"/></svg></span>
      </div>
      <div class="abs tooltip">Open</div>
      <div class="row" style="top:145px"><span class="c-check"></span><span class="c-icon" style="background:#ea4335"></span><span class="c-name">Searchly</span><span class="c-user">rkestrel@inboxly.net</span><span class="c-url">https://exchange.lumora.net</span></div>
      <div class="abs divider" style="top:185px"></div>
      <div class="row" style="top:192px"><span class="c-check"></span><span class="c-icon" style="background:#1877f2"></span><span class="c-name">Kinfold</span><span class="c-user">rkestrel12@inboxly.net</span><span class="c-url">https://www.kinfold.com</span></div>
      <div class="abs divider" style="top:229px"></div>
      <div class="row" style="top:231px"><span class="c-check"></span><span class="c-icon" style="background:#f5a623"></span><span class="c-name">Parcelo</span><span class="c-user">rkestrel@inboxly.net</span><span class="c-url">https://www.parcelo.com</span></div>
    </div>
  </main>
</section>

<!-- Light theme window -->
<section class="win win--light">
  <div class="abs logo"><span class="logo-dot"></span>Veltrika</div>
  <div class="abs search">Find something...<svg width="11" height="11" viewBox="0 0 12 12" fill="none" stroke="currentColor" stroke-width="1.2"><circle cx="5.5" cy="5.5" r="4.3"/><path d="M8.6 8.6 11 11"/></svg></div>
  <svg class="abs top-icon" style="left:630px" viewBox="0 0 18 18"><path d="M9 2a5 5 0 0 0-5 5v4l-1.5 2.5h13L14 11V7a5 5 0 0 0-5-5z" fill="var(--blue)"/><path d="M7 15a2 2 0 0 0 4 0z" fill="var(--blue)"/><circle cx="14" cy="3.5" r="2" fill="var(--green)"/></svg>
  <svg class="abs top-icon" style="left:685px" viewBox="0 0 18 18"><circle cx="9" cy="9" r="5.5" fill="none" stroke="var(--blue)" stroke-width="3.4" stroke-dasharray="2.6 1.7"/><circle cx="9" cy="9" r="4.4" fill="var(--blue)"/><circle cx="9" cy="9" r="1.8" fill="var(--win-bg)"/></svg>
  <div class="abs avatar" role="img" aria-label="User profile photo"></div>
  <div class="abs caret"></div>

  <ul class="abs nav">
    <li class="nav-item"><svg viewBox="0 0 13 13"><rect x="0" y="0" width="5" height="7" rx="1" fill="var(--blue)"/><rect x="0" y="8" width="5" height="5" rx="1" fill="var(--green)"/><rect x="7" y="0" width="6" height="13" rx="1" fill="var(--text)"/></svg>Dashboard</li>
    <li class="nav-item"><svg viewBox="0 0 13 13"><circle cx="6.5" cy="3.5" r="3" fill="var(--blue)"/><path d="M1 13a5.5 5 0 0 1 11 0z" fill="var(--blue)"/></svg>Users</li>
    <li class="nav-item"><svg viewBox="0 0 13 13"><circle cx="5" cy="3.5" r="2.8" fill="var(--blue)"/><path d="M0 12a5 4.5 0 0 1 10 0z" fill="var(--blue)"/><circle cx="10" cy="5" r="2" fill="var(--green)"/></svg>Teams</li>
    <li class="nav-item"><svg viewBox="0 0 13 13"><rect x="0" y="0" width="6" height="5" rx="1" fill="var(--blue)"/><rect x="7" y="8" width="6" height="5" rx="1" fill="var(--green)"/><path d="M3 5v5h4" stroke="var(--blue)" fill="none"/></svg>Client Containers</li>
    <li class="nav-item nav-item--active"><svg viewBox="0 0 13 13"><circle cx="6.5" cy="6.5" r="6" fill="var(--green)"/><path d="M.5 6.5h12M6.5.5c-3 3-3 9 0 12M6.5.5c3 3 3 9 0 12" stroke="var(--win-bg)" stroke-width=".9" fill="none"/></svg>Web Logins</li>
    <li class="nav-item"><svg viewBox="0 0 13 13"><path d="M2 0h6l3 3v10H2z" fill="var(--blue)"/><path d="M4 6h5M4 8h5M4 10h5" stroke="var(--win-bg)" stroke-width=".8"/></svg>Reports</li>
  </ul>
  <div class="abs version">Version 2.3.4</div>

  <main class="abs pane">
    <h1 class="abs page-title">Web Logins</h1>
    <p class="abs page-sub">Showing details of all the web logins saved in your system</p>
    <div class="abs btn-new"><svg width="8" height="8" viewBox="0 0 8 8" stroke="#fff" stroke-width="1.4"><path d="M4 0v8M0 4h8"/></svg>New</div>

    <div class="abs card">
      <h2 class="abs card-title">Lists</h2>
      <p class="abs card-meta" style="left:253px">Showing 1-10 of 354 items</p>
      <p class="abs card-meta" style="left:518px">Page<span class="page-box">1</span> / 36</p>

      <div class="row row--head"><span class="c-check"></span><span class="c-name">Name</span><span class="c-user">User name</span><span class="c-url">Login page URL</span></div>

      <div class="row" style="top:70px"><span class="c-check"></span><span class="c-icon" style="background:#1877f2"></span><span class="c-name">Kinfold</span><span class="c-user">rkestrel@inboxly.net</span><span class="c-url">https://www.kinfold.com</span></div>
      <div class="row row--hover" style="top:107px"><span class="c-check"></span><span class="c-icon" style="background:var(--text)"></span><span class="c-name">Codehive</span><span class="c-user">rkestrel@inboxly.net</span><span class="c-url">https://www.codehive.com/login</span>
        <span class="act-open"><svg class="act" viewBox="0 0 13 13" fill="none" stroke="var(--text)" stroke-width="1"><path d="M1 4V1h3M9 1h3v3M12 9v3H9M4 12H1V9"/><circle cx="5" cy="6.5" r="1.4"/><path d="M6.4 6.5H10"/></svg></span>
        <span class="act-edit"><svg class="act" viewBox="0 0 13 13" fill="none" stroke="var(--text)" stroke-width="1.1"><path d="M6 2H1.5v9.5H11V7"/><path d="M10 1l2 2-5.5 5.5H4.5v-2z"/></svg></span>
        <span class="act-del"><svg class="act" viewBox="0 0 13 13" fill="var(--text)"><rect x="1.5" y="1.5" width="10" height="1.6"/><rect x="5" y="0" width="3" height="1.5"/><path d="M2.5 4h8l-.7 9H3.2z"/></svg></span>
      </div>
      <div class="abs tooltip">Open</div>
      <div class="row" style="top:145px"><span class="c-check"></span><span class="c-icon" style="background:#ea4335"></span><span class="c-name">Searchly</span><span class="c-user">rkestrel@inboxly.net</span><span class="c-url">https://exchange.lumora.net</span></div>
      <div class="abs divider" style="top:185px"></div>
      <div class="row" style="top:192px"><span class="c-check"></span><span class="c-icon" style="background:#1877f2"></span><span class="c-name">Kinfold</span><span class="c-user">rkestrel12@inboxly.net</span><span class="c-url">https://www.kinfold.com</span></div>
      <div class="abs divider" style="top:229px"></div>
      <div class="row" style="top:231px"><span class="c-check"></span><span class="c-icon" style="background:#f5a623"></span><span class="c-name">Parcelo</span><span class="c-user">rkestrel@inboxly.net</span><span class="c-url">https://www.parcelo.com</span></div>
    </div>
  </main>
</section>

</body>
</html>
```